Animal Eye Clinic needs a Business card

We are a new veterinary ophthalmology practice (Ridgeline Pet Vision Care) and we need a business card designed. We only see animal eyes - we are not a regular veterinary clinic. We already have a logo. We are looking for a professional, good looking business card to hand out to our clients. We are looking for something simple but professional and contemporary. Our logo is likely the only picture/graphic that needs to be on the card.
Updates

Contact Information for Business Card

Delia Vossman, BSc, DVM, MSc, DipACVO
Veterinary Ophthalmologist

Phone: 250.418.3927
Email: ridgelinepetvisioncare@mailbox-example.net
Website: ridgelinepetvisioncare-example.net
Address: 1874 Thornbury Rd
Kelowna, BC, V1X 4M9

Colors

Designer to choose colors to be used in the design.

Requirements
Must have
• Our logo (attached)

```html
<!DOCTYPE html>
<html lang="en">
<head>
<meta charset="utf-8">
<title>Ridgeline Pet Vision Care – Business Card</title>
<link rel="stylesheet" href="https://fonts.googleapis.com/css2?family=Oswald:wght@500&family=Roboto:wght@300;400;500&display=swap">
<style>
  :root {
    --backdrop: #2b2b2b;
    --card: #262626;
    --card-faint: #2e2e2e;
    --teal: #0a9aab;
    --text: #f1f1f1;
    --rule: #cfcfcf;
  }
  * { box-sizing: border-box; margin: 0; padding: 0; }
  html, body { width: 1200px; height: 901px; overflow: hidden; }
  body {
    background: var(--backdrop);
    font-family: "Roboto", Arial, sans-serif;
    color: var(--text);
    position: relative;
  }
  .card {
    position: absolute;
    left: 280px;
    width: 640px;
    height: 366px;
    background: var(--card);
    overflow: hidden;
  }
  .card--front { top: 50px; }
  .card--back { top: 470px; }

  /* Front */
  .front-decoration {
    position: absolute;
    right: -70px;
    top: 40px;
    width: 330px;
    height: 330px;
    border-radius: 50%;
    background: var(--card-faint);
  }
  .brand {
    position: absolute;
    left: 150px;
    top: 128px;
    display: flex;
    align-items: center;
    gap: 18px;
  }
  .brand-mark {
    width: 58px;
    height: 58px;
    border-radius: 50%;
    background: var(--teal);
    flex: none;
  }
  .brand-name {
    color: var(--teal);
    font-weight: 500;
    font-size: 27px;
    line-height: 1.12;
    text-transform: uppercase;
  }

  /* Back */
  .person {
    position: absolute;
    left: 10px;
    top: 94px;
    width: 290px;
    text-align: right;
  }
  .person-name {
    font-family: "Oswald", "Arial Narrow", sans-serif;
    font-weight: 500;
    font-size: 16px;
    line-height: 22px;
    color: var(--teal);
    text-transform: uppercase;
    white-space: nowrap;
  }
  .person-role {
    font-weight: 300;
    font-size: 15px;
    margin-top: 4px;
  }
  .divider {
    position: absolute;
    left: 312px;
    top: 94px;
    width: 1px;
    height: 60px;
    background: var(--rule);
  }
  .contact {
    position: absolute;
    left: 326px;
    top: 95px;
    list-style: none;
    font-weight: 300;
    font-size: 12.5px;
    line-height: 20px;
  }
  .contact li { display: flex; align-items: center; gap: 7px; white-space: nowrap; }
  .contact .icon { width: 12px; height: 12px; flex: none; }
  .contact .icon-fill { fill: var(--teal); }
  .contact .icon-cut { fill: none; stroke: var(--card); stroke-width: 2; }
  .contact .accent { color: var(--teal); }
  .address {
    position: absolute;
    left: 0;
    right: 0;
    top: 268px;
    text-align: center;
    font-weight: 300;
    font-size: 17px;
  }
  .band {
    position: absolute;
    left: 0;
    right: 0;
    bottom: 0;
    height: 13px;
    background: var(--teal);
  }
</style>
</head>
<body>

<section class="card card--front">
  <div class="front-decoration" role="img" aria-label="Faint enlarged brand mark area"></div>
  <div class="brand">
    <span class="brand-mark" aria-hidden="true"></span>
    <p class="brand-name">Ridgeline<br>Pet Vision Care</p>
  </div>
</section>

<section class="card card--back">
  <div class="person">
    <h1 class="person-name">Delia Vossman, BSc, DVM, MSc, DipACVO</h1>
    <p class="person-role">Veterinary Ophthalmologist</p>
  </div>
  <div class="divider"></div>
  <ul class="contact">
    <li>
      <svg class="icon" viewBox="0 0 24 24" aria-hidden="true"><path class="icon-fill" d="M20 15.5c-1.25 0-2.45-.2-3.57-.57a1.02 1.02 0 0 0-1.02.24l-2.2 2.2a15.05 15.05 0 0 1-6.59-6.59l2.2-2.21a.96.96 0 0 0 .25-1A11.4 11.4 0 0 1 8.5 4c0-.55-.45-1-1-1H4c-.55 0-1 .45-1 1 0 9.39 7.61 17 17 17 .55 0 1-.45 1-1v-3.5c0-.55-.45-1-1-1z"/></svg>
      250.418.3927
    </li>
    <li>
      <svg class="icon" viewBox="0 0 24 24" aria-hidden="true"><rect class="icon-fill" x="2" y="5" width="20" height="14"/><path class="icon-cut" d="M2 6l10 7 10-7"/></svg>
      ridgelinepetvisioncare@mailbox-example.net
    </li>
    <li>
      <svg class="icon" viewBox="0 0 24 24" aria-hidden="true"><circle class="icon-fill" cx="12" cy="12" r="10"/></svg>
      <span>www.<span class="accent">ridgelinepetvisioncare-example</span>.net</span>
    </li>
  </ul>
  <p class="address">1874 Thornbury Rd, Kelowna, BC, V1X 4M9</p>
  <div class="band"></div>
</section>

</body>
</html>
```